Tovella Fireworks needs a web design and logo

We need a web design and logo for a fireworks business in Sydney Australia, we do public display, weddings, tv, theatrical, clubs and any other organisation that wants to do something special.
Name is Marrowind Fireworks & Pyrotechnics

```html
<!DOCTYPE html>
<html lang="en">
<head>
<meta charset="utf-8">
<title>Marrowind Fireworks &amp; Pyrotechnics</title>
<link href="https://fonts.googleapis.com/css2?family=Lora:ital,wght@0,400;0,700;1,400&display=swap" rel="stylesheet">
<style>
:root{
  --red:#c4000b;
  --red-dark:#a80009;
  --ink:#1e1e1e;
  --text:#555555;
  --muted:#8d8d8d;
  --footer:#1b1b1b;
  --white:#ffffff;
  --line:#d9d9d9;
}
*{margin:0;padding:0;box-sizing:border-box}
html,body{width:1200px;height:2258px;overflow:hidden;background:var(--white)}
body{position:relative;font-family:"Lora",Georgia,serif;color:var(--text)}
.abs{position:absolute}
a{color:inherit;text-decoration:none}

/* header */
.brand{left:99px;top:36px;font-size:27px;font-weight:700;color:var(--ink);line-height:1.25;width:340px}
.top-links{right:100px;top:22px;display:flex;gap:22px;font-size:13px;color:#444}
.top-links span{display:flex;align-items:center;gap:6px}
.top-links svg{width:12px;height:12px;fill:#444}
.search{left:848px;top:84px;width:171px;height:27px;background:var(--ink)}
.search svg{position:absolute;right:12px;top:6px;width:15px;height:15px}
.cart{left:1062px;top:74px;width:38px;height:38px}

/* nav */
.nav{left:0;top:135px;width:1200px;height:55px;background:var(--red)}
.nav ul{list-style:none;position:absolute;left:98px;top:0;display:flex;height:55px}
.nav li{width:143px;height:55px;display:flex;align-items:center;justify-content:center;color:var(--white);font-size:13px;font-weight:700;border-right:1px solid rgba(0,0,0,.18)}
.nav li:last-child{border-right:none}
.nav li.current{color:var(--ink)}

/* hero */
.hero{left:0;top:190px;width:1200px;height:451px;
  background:
    radial-gradient(circle at 18% 25%,rgba(214,150,60,.75) 0,rgba(214,150,60,0) 22%),
    radial-gradient(circle at 88% 22%,rgba(240,170,70,.8) 0,rgba(240,170,70,0) 24%),
    radial-gradient(circle at 48% 40%,rgba(170,90,120,.55) 0,rgba(170,90,120,0) 28%),
    radial-gradient(circle at 75% 80%,rgba(200,120,50,.55) 0,rgba(200,120,50,0) 25%),
    radial-gradient(circle at 30% 85%,rgba(150,70,100,.5) 0,rgba(150,70,100,0) 22%),
    linear-gradient(180deg,#2a1a14,#1a0f0c)}
.hero-title{left:99px;top:286px;font-size:60px;font-weight:700;color:var(--white);line-height:1}
.hero-sub{left:99px;top:352px;font-size:36px;font-weight:700;color:var(--red);line-height:1}
.hero-text{left:99px;top:418px;width:340px;font-size:13.5px;font-style:italic;color:var(--white);line-height:21px}
.btn-red{left:99px;top:512px;width:125px;height:38px;background:var(--red);border:2px solid var(--white);border-radius:3px;color:var(--white);font-size:12.5px;font-weight:700;display:flex;align-items:center;justify-content:center}
.arrow{width:36px;height:36px;top:398px}

/* sections */
.center{left:0;width:1200px;text-align:center}
.h2{font-size:36px;font-weight:700;color:#3a3a3a;line-height:1}
.kicker{font-size:12.5px;font-weight:700;color:var(--red)}
.lead{left:240px;width:720px;top:790px;text-align:center;font-size:14px;line-height:30px;color:var(--text)}
.btn-outline{left:539px;top:918px;width:122px;height:41px;border:1px solid #9a9a9a;color:#222;font-size:12.5px;font-weight:700;display:flex;align-items:center;justify-content:center}

.promo{top:1010px;width:298px;height:214px;display:flex;flex-direction:column;align-items:center;padding-top:70px;color:var(--white);box-shadow:0 1px 3px rgba(0,0,0,.3)}
.promo p{font-size:18.5px;font-weight:700;line-height:30px;text-align:center}
.promo span{margin-top:10px;width:104px;height:37px;border:2px solid var(--white);border-radius:3px;font-size:14px;font-weight:700;display:flex;align-items:center;justify-content:center}
.promo-1{left:98px;background:linear-gradient(180deg,#1c1a3a 0%,#3a1d4a 50%,#0d1020 100%)}
.promo-2{left:452px;background:linear-gradient(180deg,#2a1208 0%,#5a1a22 55%,#140808 100%)}
.promo-3{left:804px;background:linear-gradient(180deg,#2a2434 0%,#3b3c58 55%,#2a2c3e 100%)}

.band{left:0;top:1284px;width:1200px;height:188px;
  background:
    radial-gradient(circle at 10% 40%,rgba(200,140,60,.6) 0,rgba(200,140,60,0) 25%),
    radial-gradient(circle at 90% 50%,rgba(210,150,70,.6) 0,rgba(210,150,70,0) 25%),
    linear-gradient(180deg,#2b1c12,#1f140e)}
.band-title{top:1338px;font-size:38px;font-weight:700;color:var(--white);line-height:1}
.band-sub{top:1397px;font-size:16px;font-weight:700;color:var(--white)}

.service{top:1650px;width:207px}
.service .photo{height:187px}
.service h3{margin-top:18px;text-align:center;font-size:17px;font-weight:700;color:#222}
.s1 .photo{background:radial-gradient(circle at 65% 30%,#b8503a 0,#3a0c06 35%,#0a0404 70%)}
.s2 .photo{background:radial-gradient(circle at 50% 28%,#d0223a 0,#4a0812 35%,#120306 70%)}
.s3 .photo{background:radial-gradient(circle at 50% 30%,#5a8a7a 0,#1e3a3a 40%,#060a0a 75%)}
.s4 .photo{background:radial-gradient(circle at 50% 30%,#7ab8d0 0,#1c4a66 40%,#061420 75%)}

/* footer */
.footer{left:0;top:1929px;width:1200px;height:229px;background:var(--footer)}
.f-col{top:1956px}
.f-col h4{font-size:17px;font-weight:700;color:var(--white);margin-bottom:16px}
.f-col p,.f-col li{font-size:12px;line-height:22px;color:var(--muted)}
.f-col ul{list-style:none}
.f-col li::before{content:"›";color:var(--red);font-size:15px;margin-right:7px}
.f-col .hot{color:var(--red)}
.thumbs{display:grid;grid-template-columns:repeat(3,63px);gap:11px 17px}
.thumbs div{height:63px;border:1px solid #333}
.t1{background:radial-gradient(circle,#b04a3a,#1a0a08 70%)}
.t2{background:radial-gradient(circle,#c02a3a,#14060a 70%)}
.t3{background:radial-gradient(circle,#c05a8a,#1a0a14 70%)}
.t4{background:radial-gradient(circle,#d09a40,#2a1408 70%)}
.t5{background:radial-gradient(circle,#e0b060,#3a2410 70%)}
.t6{background:radial-gradient(circle,#a04a90,#120818 70%)}

.bottom{left:0;top:2158px;width:1200px;height:100px;background:var(--red);color:var(--white)}
.copy{left:100px;top:2182px;font-size:13px;color:var(--white)}
.social{left:100px;top:2213px;display:flex;gap:9px}
.social span{width:14px;height:14px;border-radius:50%;background:var(--white)}
.help{left:899px;top:2173px;font-size:13.5px;color:var(--white)}
.bottom-links{right:99px;top:2211px;display:flex;font-size:12px;color:var(--white)}
.bottom-links span{padding:0 8px;border-left:1px solid rgba(255,255,255,.7);line-height:14px}
.bottom-links span:first-child{border-left:none}
.bottom-links span:last-child{padding-right:0}
</style>
</head>
<body>

<header>
  <div class="abs brand">Marrowind Fireworks &amp; Pyrotechnics</div>
  <div class="abs top-links">
    <span><svg viewBox="0 0 12 12"><rect x="2" y="5" width="8" height="7" rx="1"/><path d="M3.5 5V3.5a2.5 2.5 0 0 1 5 0V5" stroke="#444" stroke-width="1.4" fill="none"/></svg>Login</span>
    <span><svg viewBox="0 0 12 12"><path d="M1 3h8l-2-2M11 9H3l2 2" stroke="#444" stroke-width="1.4" fill="none"/></svg>Compare</span>
    <span><svg viewBox="0 0 12 12"><path d="M6 11 1.2 6.2A2.8 2.8 0 0 1 6 2.4a2.8 2.8 0 0 1 4.8 3.8Z"/></svg>Wishlist</span>
    <span><svg viewBox="0 0 12 12"><circle cx="6" cy="3.5" r="2.7"/><path d="M1 12a5 5 0 0 1 10 0Z"/></svg>My Account</span>
  </div>
  <div class="abs search">
    <svg viewBox="0 0 16 16"><circle cx="6.5" cy="6.5" r="4.8" stroke="#fff" stroke-width="2" fill="none"/><path d="m10 10 4.5 4.5" stroke="#fff" stroke-width="2.4"/></svg>
  </div>
  <svg class="abs cart" viewBox="0 0 38 38" aria-label="Cart">
    <polygon fill="#c4000b" points="19,1 24,6 31,6 31,13 37,19 31,25 31,32 24,32 19,37 14,32 7,32 7,25 1,19 7,13 7,6 14,6"/>
    <path d="M11 13h3l2 9h9l2-7H15" stroke="#fff" stroke-width="1.8" fill="none"/>
    <circle cx="17" cy="25" r="1.5" fill="#fff"/><circle cx="24" cy="25" r="1.5" fill="#fff"/>
  </svg>
</header>

<nav class="abs nav">
  <ul>
    <li class="current">HOME</li>
    <li>ABOUT »</li>
    <li>PORTFOLIO »</li>
    <li>STORE »</li>
    <li>BLOG</li>
    <li>CATEGORIES»</li>
    <li>CONTACTS</li>
  </ul>
</nav>

<section>
  <div class="abs hero" role="img" aria-label="Night sky filled with golden and pink firework bursts"></div>
  <div class="abs hero-title">MARROWIND</div>
  <div class="abs hero-sub">FIREWORKS &amp; PYROTECHNICS</div>
  <p class="abs hero-text">Lorem Ipsum is simply dummy text of the printing and typesetting industry. Lorem Ipsum has been the industry's standard dummy .</p>
  <div class="abs btn-red">READ MORE</div>
  <svg class="abs arrow" style="left:26px" viewBox="0 0 36 36"><circle cx="18" cy="18" r="16" fill="none" stroke="#fff" stroke-width="2.5"/><path d="M21 10 13 18l8 8Z" fill="#fff"/></svg>
  <svg class="abs arrow" style="left:1138px" viewBox="0 0 36 36"><circle cx="18" cy="18" r="16" fill="none" stroke="#fff" stroke-width="2.5"/><path d="M15 10l8 8-8 8Z" fill="#fff"/></svg>
</section>

<section>
  <h2 class="abs center h2" style="top:693px">WELCOME</h2>
  <p class="abs center kicker" style="top:747px">NEQUE PORRO QUISQUAM EST QUI DOLOREM IPSUM QUIA DOLOR SIT AMET</p>
  <p class="abs lead">Lorem Ipsum is simply dummy text of the printing and typesetting industry. Lorem Ipsum has been the industry's standard dummy text ever since the 1500s, when an unknown printer took a galley of type and scrambled it to make a type specimen book.Lorem Ipsum is simply dummy text of the printing .</p>
  <div class="abs btn-outline">ABOUT US</div>

  <div class="abs promo promo-1" role="img" aria-label="Fireworks over a city harbour skyline"><p>Lorem Ipsum is simply<br>dummy text of the printing.</p><span>SHOP NOW</span></div>
  <div class="abs promo promo-2" role="img" aria-label="Crowd watching colourful fireworks"><p>Lorem Ipsum is simply<br>dummy text of the printing.</p><span>SHOP NOW</span></div>
  <div class="abs promo promo-3" role="img" aria-label="Fireworks above a city waterfront at dusk"><p>Lorem Ipsum is simply<br>dummy text of the printing.</p><span>SHOP NOW</span></div>
</section>

<section>
  <div class="abs band" role="img" aria-label="Golden firework bursts banner"></div>
  <h2 class="abs center band-title">PYROTECHNICS</h2>
  <p class="abs center band-sub">LOREM IPSUM IS SIMPLY DUMMY TEXT OF THE PRINTING.</p>
</section>

<section>
  <h2 class="abs center h2" style="top:1520px">OUR SERVICES</h2>
  <p class="abs center kicker" style="top:1572px">NEQUE PORRO QUISQUAM EST QUI DOLOREM IPSUM QUIA DOLOR SIT AMET</p>
  <div class="abs service s1" style="left:98px"><div class="photo" role="img" aria-label="Red firework bursts at a wedding"></div><h3>WEDDINGS</h3></div>
  <div class="abs service s2" style="left:361px"><div class="photo" role="img" aria-label="Red firework over a harbour city"></div><h3>PUBLIC DISPLAY</h3></div>
  <div class="abs service s3" style="left:625px"><div class="photo" role="img" aria-label="Crowd silhouettes under green fireworks"></div><h3>CLUBS</h3></div>
  <div class="abs service s4" style="left:894px"><div class="photo" role="img" aria-label="Blue and white fireworks over spectators"></div><h3>THEATRICAL</h3></div>
</section>

<footer>
  <div class="abs footer"></div>
  <div class="abs f-col" style="left:101px;width:210px">
    <h4>ABOUT US</h4>
    <p>Contrary to popular belief, Lorem Ipsum is not simply random text. It has roots in a piece of classical Latin literature from 45 BC, making it over 2000 years old.</p>
  </div>
  <div class="abs f-col" style="left:357px">
    <h4>TERMS &amp; CONDITIONS</h4>
    <ul>
      <li>Shipping &amp; taxes</li><li>Return policy</li><li>Careers</li><li>Affiliates</li><li>Legal Notice</li><li>Privacy &amp; Security</li><li>Sitemap</li>
    </ul>
  </div>
  <div class="abs f-col" style="left:610px">
    <h4>PHOTO STREAM</h4>
    <div class="thumbs">
      <div class="t1" role="img" aria-label="Firework photo"></div>
      <div class="t2" role="img" aria-label="Firework photo"></div>
      <div class="t3" role="img" aria-label="Firework photo"></div>
      <div class="t4" role="img" aria-label="Firework photo"></div>
      <div class="t5" role="img" aria-label="Firework photo"></div>
      <div class="t6" role="img" aria-label="Firework photo"></div>
    </div>
  </div>
  <div class="abs f-col" style="left:891px;width:215px">
    <h4>CONTACT US</h4>
    <p>Alden Perrow, a Latin professor at Kestrel Hill College</p>
    <p style="margin-top:6px">To order: <span class="hot">+12 480 3157</span></p>
    <p style="margin-top:6px">Client support: <span class="hot">+12 706 2284</span></p>
    <p style="margin-top:6px">Email: orders@marrowindfireworks.com</p>
  </div>

  <div class="abs bottom"></div>
  <p class="abs copy">© 2015 Marrowind Fireworks &amp; Pyrotechnics. All rights reserved</p>
  <div class="abs social" aria-label="Social links"><span></span><span></span><span></span><span></span><span></span><span></span></div>
  <p class="abs help">Need Help:(512) 403-2916</p>
  <div class="abs bottom-links"><span>Home</span><span>About US</span><span>FAQ</span><span>Blog</span><span>Join Our Newsletter</span><span>Privacy</span></div>
</footer>

</body>
</html>
```